Develop website for Cloud Security Startup

Looking for a logo that conveys the outsourced security and management of clients data, systems and development in Tellix, Bri and Pindle with an emphasis on security and compliance

Target Market(s)

Companies looking for professional services IT firm

Coding

Coded - Design and coding required

Number of Pages Required

5+ page

Font styles to use
Sans Serif

Colors
0455a3
33a6d7

Requirements
Must have
• Landing Page
- Help me get started

Move to the cloud safely
- Benefits of Cloud

What we do
- Cloud Adoption
- Managed Services
- Optimise

Resources
- News
- Resources
- Events
- Webinars
- Not for profit
- Case Studies
- Support Button
- Incident Button

Company
- About Us
- Why Vorplexa?
- Acreditations
- Quorvane Tellix Partner
- Net Promoter Score
- Careers
- Contact Us

Contact Us

```html
<!DOCTYPE html>
<html lang="en">
<head>
<meta charset="utf-8">
<title>Vorplexa – Cloud Security</title>
<link href="https://fonts.googleapis.com/css2?family=Montserrat:wght@400;500;600;700;800&family=Poppins:wght@700;800&display=swap" rel="stylesheet">
<style>
:root{
  --navy:#0a3f98;
  --brand:#0455a3;
  --sky:#33a6d7;
  --sky-btn:#2f97dc;
  --ink:#141a2b;
  --pale:#e8f3fc;
  --pale-footer:#e2f0fb;
  --white:#ffffff;
  --night:#050a1c;
}
*{box-sizing:border-box;margin:0;padding:0}
html,body{width:1200px;height:3977px;overflow:hidden}
body{font-family:"Montserrat",Arial,sans-serif;color:var(--ink);background:var(--white);position:relative}
.abs{position:absolute}
.btn{position:absolute;display:flex;align-items:center;justify-content:center;background:var(--sky-btn);color:var(--white);font-weight:700;border-radius:6px;text-transform:uppercase}
.btn-sm{font-size:11px;height:30px;border-radius:5px}
.bar{position:absolute;width:40px;height:4px;background:var(--sky);border-radius:2px}
.section-title{position:absolute;left:0;width:1200px;text-align:center;font-family:"Poppins",sans-serif;font-weight:800;font-size:25px;letter-spacing:-.2px}

/* header */
.site-header{position:absolute;top:0;left:0;width:1200px;height:116px;background:var(--white)}
.brand{position:absolute;left:134px;top:56px;display:flex;align-items:center;gap:8px;font-weight:700;font-size:22px;color:var(--brand)}
.brand-dot{width:18px;height:18px;border-radius:50%;background:var(--brand)}
.follow{position:absolute;left:712px;top:32px;display:flex;align-items:center;gap:6px;font-size:11px;font-weight:500}
.social{width:25px;height:25px;border-radius:50%;background:var(--brand);display:inline-block}
.social.alt{background:var(--sky-btn)}
.social.dark{background:#0d2753}
.call{position:absolute;left:918px;top:26px;display:flex;gap:10px;align-items:center}
.call-label{font-size:11px;color:var(--brand)}
.call-num{font-size:17px;font-weight:700;color:var(--navy)}
.nav{position:absolute;top:80px;left:452px;display:flex;gap:0;font-size:14px;font-weight:600}
.nav a{color:var(--ink);text-decoration:none;margin-right:42px;display:flex;align-items:center;gap:6px}
.nav a.active{color:var(--sky-btn)}
.nav a:last-child{margin-right:0}
.caret{width:8px;height:5px}

/* hero */
.hero{position:absolute;top:116px;left:0;width:1200px;height:601px;background:radial-gradient(ellipse at 78% 38%,#1f6fd0 0%,#0b2c78 30%,#07123a 60%,#040a22 100%)}
.hero-art{position:absolute;left:620px;top:0;width:580px;height:601px;background:radial-gradient(ellipse at 55% 40%,rgba(60,210,220,.55) 0%,rgba(40,120,230,.35) 35%,rgba(0,0,0,0) 70%)}
.hero-title{position:absolute;left:133px;top:166px;color:var(--white);font-family:"Poppins",sans-serif;font-weight:800;font-size:39px;line-height:53px}
.hero .btn{left:133px;top:355px;width:276px;height:57px;font-size:19px;text-transform:uppercase;border-radius:8px}
.dots{position:absolute;left:563px;top:551px;display:flex;gap:9px;align-items:center}
.dots span{width:6px;height:6px;border-radius:50%;background:var(--white)}
.dots span.on{width:11px;height:11px;background:none;border:2px solid var(--white)}

/* services */
.service{position:absolute;top:886px;width:300px;height:386px;color:var(--white);text-align:center}
.service svg.arch{position:absolute;left:0;top:39px}
.service .icon{position:absolute;left:105px;top:0;width:90px;height:90px;border-radius:12px;background:var(--sky-btn);display:flex;align-items:center;justify-content:center}
.service h3{position:absolute;top:131px;width:100%;font-size:17px;font-weight:700}
.service p{position:absolute;top:171px;left:45px;width:210px;font-size:13.5px;line-height:19.5px}
.service .btn{left:101px;top:320px;width:98px}

/* welcome */
.welcome{position:absolute;top:1330px;left:0;width:1200px;height:523px;background:var(--pale)}
.welcome-mark{position:absolute;left:134px;top:88px;width:368px;height:357px}
.welcome-rule{position:absolute;left:547px;top:60px;width:1px;height:410px;background:#c8d6e6}
.welcome-kicker{position:absolute;left:614px;top:53px;font-size:16px;font-weight:500}
.welcome-name{position:absolute;left:614px;top:76px;font-family:"Poppins",sans-serif;font-weight:800;font-size:38px;color:var(--brand);letter-spacing:.5px}
.welcome p{position:absolute;left:616px;top:176px;width:460px;font-size:17px;line-height:26.5px;color:#24303f}
.welcome .btn{left:619px;top:426px;width:98px}

/* benefits */
.benefits{position:absolute;top:1853px;left:0;width:1200px;height:665px;background:linear-gradient(180deg,#0a49a6 0%,#0a3f98 100%);color:var(--white)}
.benefit{position:absolute;width:460px;height:90px}
.benefit .icon{position:absolute;left:0;top:0;width:90px;height:90px;border-radius:14px;background:var(--sky-btn);display:flex;align-items:center;justify-content:center}
.benefit h4{position:absolute;left:110px;top:0;font-size:17px;font-weight:700}
.benefit p{position:absolute;left:111px;top:32px;width:305px;font-size:13.5px;line-height:19.5px}

/* resources */
.resource{position:absolute;top:2673px;width:297px;height:417px;background:var(--pale)}
.resource .photo{height:187px}
.resource h5{position:absolute;left:28px;top:220px;font-size:14.5px;font-weight:600;line-height:20px}
.resource p{position:absolute;left:28px;top:267px;width:230px;font-size:12px;line-height:18px}
.resource .btn{left:28px;top:355px;width:88px;height:29px;font-size:10.5px}

/* careers */
.careers{position:absolute;top:3127px;left:0;width:1200px;height:503px;background:var(--night)}
.careers-art{position:absolute;left:430px;top:0;width:770px;height:503px;background:radial-gradient(ellipse at 42% 58%,#5ee6ff 0%,#178ec2 22%,#0a3a66 48%,rgba(5,10,28,0) 75%)}
.careers h2{position:absolute;left:0;width:555px;top:102px;text-align:center;color:var(--white);font-family:"Poppins",sans-serif;font-weight:800;font-size:25px}
.careers p{position:absolute;left:130px;width:295px;top:197px;text-align:center;color:var(--white);font-size:20px;line-height:26px}
.careers .btn{left:222px;top:363px;width:122px;height:38px;font-size:13.5px}

/* footer */
.site-footer{position:absolute;top:3630px;left:0;width:1200px;height:347px;background:var(--pale-footer)}
.footer-brand{position:absolute;left:134px;top:168px;display:flex;align-items:center;gap:12px;font-weight:700;font-size:40px;color:var(--brand)}
.footer-brand .brand-dot{width:34px;height:34px}
.fcol h6{font-size:13px;font-weight:700;margin-bottom:26px}
.fcol{position:absolute;top:55px;font-size:11.5px;line-height:20px}
.fcol li{list-style:none}
.fitem{display:flex;gap:12px;align-items:flex-start;margin-bottom:18px;line-height:16px}
.fitem .pin{width:22px;height:22px;border-radius:50%;background:var(--sky-btn);flex:none;display:flex;align-items:center;justify-content:center;margin-top:3px}
.footer-rule{position:absolute;left:134px;top:280px;width:932px;height:1px;background:#cfdded}
.copy{position:absolute;top:303px;left:0;width:1200px;text-align:center;font-size:9px}
</style>
</head>
<body>

<header class="site-header">
  <div class="brand"><span class="brand-dot"></span>VORPLEXA</div>
  <div class="follow">FOLLOW US
    <span class="social" style="margin-left:8px"></span><span class="social alt"></span><span class="social dark"></span>
  </div>
  <div class="call">
    <svg width="28" height="28" viewBox="0 0 28 28"><circle cx="14" cy="14" r="12.5" fill="none" stroke="#0d2753" stroke-width="1.8"/><path d="M10 8.5l2.2-.5 1.3 3-1.5 1.1a7 7 0 0 0 3.9 3.9l1.1-1.5 3 1.3-.5 2.2c-5.5.4-9.9-4-9.5-9.5z" fill="#0d2753"/></svg>
    <div><div class="call-label">CALL US</div><div class="call-num">555.014.2290</div></div>
  </div>
  <nav class="nav">
    <a class="active">HOME</a>
    <a>WHAT WE DO <svg class="caret" viewBox="0 0 8 5"><path d="M0 0l4 4 4-4" fill="none" stroke="#141a2b" stroke-width="1.3"/></svg></a>
    <a>RESOURCES <svg class="caret" viewBox="0 0 8 5"><path d="M0 0l4 4 4-4" fill="none" stroke="#141a2b" stroke-width="1.3"/></svg></a>
    <a>COMPANY <svg class="caret" viewBox="0 0 8 5"><path d="M0 0l4 4 4-4" fill="none" stroke="#141a2b" stroke-width="1.3"/></svg></a>
    <a>CONTACT US</a>
  </nav>
</header>

<section class="hero">
  <div class="hero-art" role="img" aria-label="Glowing digital cloud with a keyhole, streaming binary code"></div>
  <h1 class="hero-title">CLOUD SECURITY<br>STARTUP OUTSOURCING<br>SECURITY</h1>
  <a class="btn">Help me get started</a>
  <div class="dots"><span></span><span></span><span class="on"></span><span></span><span></span></div>
</section>

<div class="bar" style="left:580px;top:765px"></div>
<h2 class="section-title" style="top:782px">WHAT WE DO</h2>
<div class="bar" style="left:580px;top:829px"></div>

<article class="service" style="left:125px">
  <svg class="arch" width="300" height="347" viewBox="0 0 300 347"><path d="M0 45Q150-45 300 45V347H0Z" fill="#0a43a0"/></svg>
  <div class="icon"><svg width="52" height="52" viewBox="0 0 52 52" fill="none" stroke="#fff" stroke-width="2.2"><path d="M18 22a6 6 0 0 1 1-12 8 8 0 0 1 15 2 5 5 0 0 1 0 10z"/><path d="M6 30l6 12h8v-6l-7-8M46 30l-6 12h-8v-6l7-8"/></svg></div>
  <h3>CLOUD ADOPTION</h3>
  <p>There are many variations of passages of Lorem Ipsum avail able, but the majority have suffer ed alteration in some form, by injected humour, or rand omised words</p>
  <a class="btn btn-sm">Read more</a>
</article>
<article class="service" style="left:450px">
  <svg class="arch" width="300" height="347" viewBox="0 0 300 347"><path d="M0 45Q150-45 300 45V347H0Z" fill="#0a43a0"/></svg>
  <div class="icon"><svg width="56" height="56" viewBox="0 0 56 56" fill="none" stroke="#fff" stroke-width="2.2"><path d="M16 40a9 9 0 0 1 0-18 12 12 0 0 1 23-2 9 9 0 0 1 1 20"/><circle cx="29" cy="32" r="5"/><path d="M29 22v4M29 38v4M19 32h4M35 32h4"/></svg></div>
  <h3>MANAGED SERVICES</h3>
  <p>There are many variations of passages of Lorem Ipsum avail able, but the majority have suffer ed alteration in some form, by injected humour, or rand omised words</p>
  <a class="btn btn-sm">Read more</a>
</article>
<article class="service" style="left:778px">
  <svg class="arch" width="300" height="347" viewBox="0 0 300 347"><path d="M0 45Q150-45 300 45V347H0Z" fill="#0a43a0"/></svg>
  <div class="icon"><svg width="52" height="52" viewBox="0 0 52 52" fill="none" stroke="#fff" stroke-width="2.2"><path d="M30 44H12V8h18l8 8v10"/><path d="M17 18h12M17 24h14M17 30h8"/><circle cx="38" cy="38" r="5"/><path d="M38 29v3M38 44v3M29 38h3M44 38h3"/></svg></div>
  <h3>OPTIMISE</h3>
  <p>There are many variations of passages of Lorem Ipsum avail able, but the majority have suffer ed alteration in some form, by injected humour, or rand omised words</p>
  <a class="btn btn-sm">Read more</a>
</article>

<section class="welcome">
  <svg class="welcome-mark" viewBox="0 0 368 357" aria-label="Vorplexa">
    <circle cx="145" cy="145" r="145" fill="#0a3f98"/>
    <text x="145" y="155" text-anchor="middle" font-family="Montserrat, sans-serif" font-weight="700" font-size="38" fill="#ffffff">VORPLEXA</text>
  </svg>
  <div class="welcome-rule"></div>
  <div class="welcome-kicker">WELCOME TO</div>
  <h2 class="welcome-name">VORPLEXA</h2>
  <div class="bar" style="left:616px;top:135px"></div>
  <p>At vero eos et accusamus et iusto odio dignissimos ducimus qui blanditiis praesentium voluptatum deleniti atque corrupti quos dolores et quas molestias excepturi sint occaecati cupiditate non provident, similique sunt in culpa qui officia deserunt mollitia animi, id est laborum et dolorum fuga. Et harum quidem rerum facilis est et expedita distinctio. Nam libero tempore, cum soluta nobis est eligendi optio cumque nihil impedit.</p>
  <a class="btn btn-sm">Read more</a>
</section>

<section class="benefits">
  <div class="bar" style="left:580px;top:53px"></div>
  <h2 class="section-title" style="top:70px;color:#fff">BENEFITS OF CLOUD</h2>
  <div class="bar" style="left:580px;top:117px"></div>

  <div class="benefit" style="left:133px;top:182px">
    <div class="icon"><svg width="44" height="44" viewBox="0 0 44 44" fill="none" stroke="#fff" stroke-width="2.2"><rect x="10" y="5" width="24" height="34" rx="2"/><path d="M15 14h14M15 20h14M15 26h14M15 32h8"/></svg></div>
    <h4>LOREM IPSUM</h4>
    <p>There are many variations of passages of Lorem Ipsum avail able, but the majority have suffer ed alteration in some form.</p>
  </div>
  <div class="benefit" style="left:661px;top:182px">
    <div class="icon"><svg width="50" height="50" viewBox="0 0 50 50" fill="none" stroke="#fff" stroke-width="2.2"><path d="M14 32a8 8 0 0 1 0-16 11 11 0 0 1 21-2 8 8 0 0 1 1 18"/><path d="M25 24v16M19 28v8M31 28v8"/><circle cx="25" cy="42" r="2"/><circle cx="19" cy="38" r="2"/><circle cx="31" cy="38" r="2"/></svg></div>
    <h4>LOREM IPSUM</h4>
    <p>There are many variations of passages of Lorem Ipsum avail able, but the majority have suffer ed alteration in some form.</p>
  </div>
  <div class="benefit" style="left:133px;top:342px">
    <div class="icon"><svg width="50" height="50" viewBox="0 0 50 50" fill="none" stroke="#fff" stroke-width="2.4"><circle cx="25" cy="25" r="7"/><path d="M25 6l4 5 6-2 1 6 6 2-2 6 4 4-5 3 1 6-6 1-2 6-6-2-4 4-3-5-6 1-1-6-6-2 2-6-4-4 5-3-1-6 6-1 2-6 6 2z"/></svg></div>
    <h4>LOREM IPSUM</h4>
    <p>There are many variations of passages of Lorem Ipsum avail able, but the majority have suffer ed alteration in some form.</p>
  </div>
  <div class="benefit" style="left:661px;top:342px">
    <div class="icon"><svg width="46" height="46" viewBox="0 0 46 46" fill="none" stroke="#fff" stroke-width="2.4"><path d="M22 9H9v28h28V24"/><path d="M34 6l6 6-16 16h-6v-6z"/></svg></div>
    <h4>LOREM IPSUM</h4>
    <p>There are many variations of passages of Lorem Ipsum avail able, but the majority have suffer ed alteration in some form.</p>
  </div>
  <div class="benefit" style="left:133px;top:502px">
    <div class="icon"><svg width="56" height="46" viewBox="0 0 56 46" fill="none" stroke="#fff" stroke-width="2.4"><path d="M14 36a10 10 0 0 1 0-20 14 14 0 0 1 27-1 10 10 0 0 1 0 21z"/><path d="M18 30a8 8 0 0 1 16-6 6 6 0 0 1 8 6"/></svg></div>
    <h4>LOREM IPSUM</h4>
    <p>There are many variations of passages of Lorem Ipsum avail able, but the majority have suffer ed alteration in some form.</p>
  </div>
  <div class="benefit" style="left:661px;top:502px">
    <div class="icon"><svg width="50" height="50" viewBox="0 0 50 50" fill="none" stroke="#fff" stroke-width="2.2"><rect x="7" y="18" width="30" height="20" rx="2"/><path d="M4 42h36"/><path d="M24 16a7 7 0 0 1 13-4 6 6 0 0 1 7 6 5 5 0 0 1-3 9h-4" fill="none"/></svg></div>
    <h4>LOREM IPSUM</h4>
    <p>There are many variations of passages of Lorem Ipsum avail able, but the majority have suffer ed alteration in some form.</p>
  </div>
</section>

<div class="bar" style="left:580px;top:2570px"></div>
<h2 class="section-title" style="top:2587px">RESOURCES</h2>
<div class="bar" style="left:580px;top:2634px"></div>

<article class="resource" style="left:130px">
  <div class="photo" role="img" aria-label="Glowing network cloud above a dark blue data field" style="background:radial-gradient(circle at 50% 50%,#2a7fd0 0%,#0d2c62 55%,#061634 100%)"></div>
  <h5>At vero eos et accusamus<br>et iusto odio dignissimos.</h5>
  <p>There are many variations of passages of Lorem Ipsum avail able, but the majority have suffer ed alteration in some form, by injected.</p>
  <a class="btn btn-sm">Read more</a>
</article>
<article class="resource" style="left:452px">
  <div class="photo" role="img" aria-label="Hands holding a glowing security shield in a cloud" style="background:radial-gradient(circle at 50% 45%,#cfe3f2 0%,#6f8fae 35%,#2b3443 75%,#1a1e26 100%)"></div>
  <h5>At vero eos et accusamus<br>et iusto odio dignissimos.</h5>
  <p>There are many variations of passages of Lorem Ipsum avail able, but the majority have suffer ed alteration in some form, by injected.</p>
  <a class="btn btn-sm">Read more</a>
</article>
<article class="resource" style="left:773px">
  <div class="photo" role="img" aria-label="Hands typing on a laptop with floating security icons" style="background:linear-gradient(135deg,#3a2f2c 0%,#7a6a63 40%,#4b4a52 70%,#22212a 100%)"></div>
  <h5>At vero eos et accusamus<br>et iusto odio dignissimos.</h5>
  <p>There are many variations of passages of Lorem Ipsum avail able, but the majority have suffer ed alteration in some form, by injected.</p>
  <a class="btn btn-sm">Read more</a>
</article>

<section class="careers">
  <div class="careers-art" role="img" aria-label="Laptop glowing with cyan cloud computing icons in the dark"></div>
  <div class="bar" style="left:258px;top:86px"></div>
  <h2>CAREERS</h2>
  <p>There are many variations of passages of Lorem Ipsum avail able, but the majority have suffer ed alteration in some form by injected.</p>
  <a class="btn">Contact us</a>
</section>

<footer class="site-footer">
  <div class="footer-brand"><span class="brand-dot"></span>VORPLEXA</div>
  <div class="fcol" style="left:483px">
    <h6>MENU</h6>
    <ul><li>HOME</li><li>WHAT WE DO</li><li>RESOURCES</li><li>COMPANY</li><li>CONTACT US</li></ul>
  </div>
  <div class="fcol" style="left:710px">
    <h6>CONTACT US</h6>
    <div class="fitem"><span class="pin"><svg width="10" height="12" viewBox="0 0 10 12"><path d="M5 0a4 4 0 0 1 4 4c0 3-4 8-4 8S1 7 1 4a4 4 0 0 1 4-4z" fill="#fff"/></svg></span><div>Halvenweg 27<br>4410 Ostra</div></div>
    <div class="fitem"><span class="pin"><svg width="11" height="11" viewBox="0 0 11 11"><path d="M1 1.5L3 1l1.3 2.6-1.2 1a6 6 0 0 0 3.3 3.3l1-1.2L10 8l-.5 2C5 10.3.7 6 1 1.5z" fill="#fff"/></svg></span><div>Call Us<br>555.014.2290</div></div>
    <div class="fitem"><span class="pin"><svg width="11" height="8" viewBox="0 0 11 8"><rect width="11" height="8" rx="1" fill="#fff"/><path d="M0 0l5.5 4L11 0" stroke="#2f97dc" fill="none"/></svg></span><div>E mail Us<br>info@vorplexa.com</div></div>
  </div>
  <div class="fcol" style="left:970px">
    <h6>FOLLOW US</h6>
    <div class="fitem"><span class="pin"></span><div>Like us on<br>FRIENDLO</div></div>
    <div class="fitem"><span class="pin"></span><div>Follow us on<br>CHIRPON</div></div>
    <div class="fitem"><span class="pin"></span><div>Follow us on<br>LINKWORK</div></div>
  </div>
  <div class="footer-rule"></div>
  <div class="copy">Copyright © 2021 All Rights Reserved</div>
</footer>

</body>
</html>
```